Lurvik.no is a new website about pedagogical entrepreneurship. It's main target group is teachers. The Nordic Bureau for Digital Schooling and the National Office for Learning and Classrooms are leading the project.

The web page is meant to show examples of how different methods of entrepreneurship can be used pedagogical in a learning environment. The page will also support the user with examples of different teaching programs and other examples of best practice.

Pedagogical entrepreneurship is not about business and men in suits. It's a method for learning. The focus in the design should be on school, education and new ways of learning.

The final product should be motivating and engaging, but at the same time governmental and serious. We are not looking for something "flashy" and corporate-looking, but a moderate, task-focused and clean design that state quality.

We need designs for three pages:
1 - frontpage
2 - subpage ("Metoder og undervisningsopplegg")
3 - subpage ("Små-TOPP i Vassbygd")

The interaction design for these three pages will be uploaded as an attachment.

We would like you to find inspiration in the following websites:
- www.skapekraft.no
- www.giellu.no
- www.brightfernlab.com
- www.zyx.no
(more will be added)

Please use the attached logo, and feel free to use this as an inspiration for the rest of the design.

Target Market(s)

Teachers

Industry/Entity Type

Education

Requirements
Must have
• * Header with: Logo. Main navigation. Utility navigation. Search box.
* Footer
Should not have
• Images of men in suits.
Very strong graphical elements that stands out too much (we want it clean).

```html
<!DOCTYPE html>
<html lang="en">
<head>
<meta charset="utf-8">
<title>Lurvik.no – Pedagogical entrepreneurship</title>
<link rel="stylesheet" href="https://fonts.googleapis.com/css2?family=Source+Sans+3:ital,wght@0,400;0,600;0,700;1,700&display=swap">
<style>
  :root {
    --page-bg: #ffffff;
    --sky-top: #c9d2d9;
    --sky-mid: #6f93a8;
    --sky-bottom: #1d5676;
    --footer-top: #5d879d;
    --footer-bottom: #174c6b;
    --brand-blue: #1a8fd6;
    --heading-blue: #2a5c90;
    --link-grey: #8a8a8a;
    --nav-grey: #c6c6c6;
    --panel-light: #f7f7f7;
    --panel-shade: #dcdcdc;
    --rule: #c8c8c8;
    --carousel-top: #4d7c95;
    --carousel-bottom: #134d6d;
    --footer-link: #a9d8f2;
    --ink-dark: #243447;
    --gauge-navy: #2e2f66;
  }
  * { box-sizing: border-box; margin: 0; padding: 0; }
  html, body { width: 1200px; height: 1117px; overflow: hidden; background: var(--page-bg); }
  body { font-family: "Source Sans 3", "Myriad Pro", Arial, sans-serif; position: relative; }
  a { color: inherit; }

  .stage {
    position: absolute; left: 48px; top: 51px; width: 1104px; height: 1008px;
    background: linear-gradient(180deg, var(--sky-top) 0%, var(--sky-mid) 45%, var(--sky-bottom) 86%);
    overflow: hidden;
  }

  /* Brand */
  .brand { position: absolute; left: 68px; top: 32px; }
  .brand-mark { position: absolute; left: 0; top: 4px; width: 62px; height: 62px; background: var(--brand-blue); border-radius: 6px; }
  .brand-name { position: absolute; left: 95px; top: -6px; font-size: 60px; font-weight: 700; color: var(--brand-blue); letter-spacing: -1px; line-height: 1; }
  .brand-tagline { position: absolute; left: 96px; top: 55px; white-space: nowrap; font-size: 9.5px; font-weight: 600; color: #fff; }

  /* Side panel */
  .side-panel {
    position: absolute; left: 69px; top: 179px; width: 340px; height: 611px;
    border-radius: 16px;
    background: linear-gradient(180deg, var(--panel-light) 0%, var(--panel-shade) 100%);
    box-shadow: 0 6px 18px rgba(0,0,0,.18);
  }
  .main-nav { position: absolute; left: 21px; top: 19px; list-style: none; }
  .main-nav li {
    width: 269px; height: 50px; margin-bottom: 9px;
    background: var(--nav-grey);
    box-shadow: 0 2px 3px rgba(0,0,0,.15);
    display: flex; align-items: center; padding-left: 59px;
    color: #fff; font-size: 11.5px; font-weight: 400; text-transform: uppercase; line-height: 1.3;
  }
  .meter { position: absolute; left: 86px; top: 287px; }
  .meter-caption { position: absolute; left: 4px; top: 423px; width: 300px; text-align: center; font-size: 10.5px; line-height: 14px; color: #9a9a9a; }
  .meter-link { position: absolute; left: 4px; top: 438px; width: 300px; text-align: center; font-size: 13.5px; line-height: 18px; font-weight: 600; color: var(--ink-dark); }

  /* Main panel */
  .main-panel {
    position: absolute; left: 359px; top: 139px; width: 713px; height: 662px;
    border-radius: 16px; overflow: hidden;
    box-shadow: 0 10px 28px rgba(0,0,0,.35);
  }
  .content { position: absolute; left: 0; top: 0; width: 713px; height: 425px; background: linear-gradient(180deg, #fff 0%, #f0f0f0 100%); }
  .utility-nav { position: absolute; left: 51px; top: 20px; font-size: 11.5px; line-height: 15px; color: var(--link-grey); }
  .utility-nav a { position: absolute; top: 0; white-space: nowrap; text-decoration: underline; }
  .search { position: absolute; left: 510px; top: 19px; width: 171px; height: 21px; border: 1px solid var(--rule); background: #fff; }
  .search span { position: absolute; left: 6px; top: 2px; font-size: 11px; color: #888; }
  .search-button { position: absolute; right: -1px; top: -1px; width: 21px; height: 21px; background: #c9c9c9; }

  .intro { position: absolute; left: 51px; top: 84px; color: var(--heading-blue); }
  .intro h1 { font-size: 18.5px; font-style: italic; font-weight: 700; line-height: 22px; }
  .intro p { font-size: 15px; line-height: 18.6px; white-space: nowrap; }
  .rule { position: absolute; left: 51px; top: 175px; width: 633px; height: 1px; background: var(--rule); }

  .get-started { position: absolute; left: 51px; top: 206px; font-size: 16.5px; line-height: 20px; font-weight: 700; color: var(--heading-blue); }
  .link-column { position: absolute; top: 240px; }
  .link-column h2 { font-size: 13.5px; line-height: 17px; font-weight: 700; color: var(--heading-blue); margin-bottom: 1px; }
  .link-column ul { list-style: none; }
  .link-column li { font-size: 13px; line-height: 19.3px; color: var(--link-grey); text-decoration: underline; }
  .link-column .more { position: absolute; left: 0; top: 131px; font-size: 10.5px; line-height: 13px; color: var(--brand-blue); text-decoration: underline; }
  .methods { left: 51px; }
  .plans { left: 222px; }
  .column-divider { position: absolute; left: 193px; top: 241px; width: 1px; height: 149px; background: var(--rule); }

  .carousel { position: absolute; left: 0; top: 425px; width: 713px; height: 237px; background: linear-gradient(180deg, var(--carousel-top) 0%, var(--carousel-bottom) 100%); }
  .carousel-arrow { position: absolute; top: 73px; }
  .slide { position: absolute; top: 37px; width: 103px; }
  .slide-image { width: 103px; height: 104px; background: linear-gradient(135deg, #ffffff 0%, #e4e4e4 55%, #f4f4f4 100%); }
  .slide-title { margin-top: 8px; font-size: 11.5px; line-height: 14px; font-weight: 700; color: #fff; }

  /* Footer */
  .site-footer {
    position: absolute; left: 0; top: 870px; width: 1104px; height: 138px;
    background: linear-gradient(180deg, var(--footer-top) 0%, var(--footer-bottom) 100%);
  }
  .footer-mark { position: absolute; left: 92px; top: 23px; width: 76px; height: 76px; background: #fff; border-radius: 6px; }
  .footer-group { position: absolute; font-size: 9px; line-height: 1.3; }
  .footer-group h3 { font-size: 9px; font-weight: 700; color: #fff; }
  .footer-group p { color: var(--footer-link); margin-bottom: 9px; white-space: nowrap; }
  .footer-group b { color: #fff; font-weight: 600; }
</style>
</head>
<body>
<div class="stage">

  <header class="brand">
    <div class="brand-mark"></div>
    <div class="brand-name">Lurvik</div>
    <div class="brand-tagline">Entreprenørielle metoder i undervisningen</div>
  </header>

  <aside class="side-panel">
    <ul class="main-nav">
      <li>What is pedagogical<br>entrepreneurship</li>
      <li>Methods and<br>teaching plans</li>
      <li>Good examples/<br>best pratice</li>
    </ul>
    <svg class="meter" width="124" height="124" viewBox="0 0 124 124" role="img" aria-label="Lurvikmeter gauge">
      <circle cx="62" cy="62" r="60" fill="#fff" stroke="#d2d2d2" stroke-width="2"/>
      <path d="M62 14 A48 48 0 0 1 110 62 L86 62 A24 24 0 0 0 62 38 Z" fill="#c4c4c4"/>
      <path d="M14 62 A48 48 0 0 0 62 110 L62 100 A38 38 0 0 1 24 62 Z" fill="var(--gauge-navy)"/>
      <circle cx="62" cy="62" r="36" fill="#d7d7d7"/>
      <circle cx="62" cy="62" r="30" fill="#bcbcbc"/>
      <line x1="62" y1="62" x2="40" y2="40" stroke="#fff" stroke-width="3" stroke-linecap="round"/>
    </svg>
    <p class="meter-caption">Are you working entrepreneurship-like?</p>
    <p class="meter-link">Try the lurvikmeter</p>
  </aside>

  <main class="main-panel">
    <section class="content">
      <nav class="utility-nav">
        <a style="left:0">best pratice school</a>
        <a style="left:120px">Try lurvikmeter</a>
        <a style="left:238px">about lurvik.no</a>
      </nav>
      <div class="search"><span>search ...</span><div class="search-button">
        <svg width="21" height="21" viewBox="0 0 21 21"><circle cx="9.5" cy="9.5" r="4" fill="none" stroke="#fff" stroke-width="1.5"/><line x1="12.5" y1="12.5" x2="16" y2="16" stroke="#fff" stroke-width="1.5"/></svg>
      </div></div>

      <div class="intro">
        <h1>Pedagogical entrepreneurship works.</h1>
        <p>Lorem ipsum dolor sit amet, consectetur adipisicing elit,<br>sed fo eiusmod tempor incididunt ut labore<br>et dolore magna aliqua.</p>
      </div>
      <div class="rule"></div>

      <h2 class="get-started">GET STARTED!</h2>
      <div class="link-column methods">
        <h2>METHODS</h2>
        <ul><li>Café-pedagogikk</li><li>elevbedrift</li><li>Gründercamp</li><li>Story line</li><li>TOPP</li></ul>
        <a class="more">more...</a>
      </div>
      <div class="column-divider"></div>
      <div class="link-column plans">
        <h2>TEACHING PLANS</h2>
        <ul><li>Lorem Ipsum</li><li>Lorem Ipsum</li><li>Lorem Ipsum</li><li>Lorem Ipsum</li></ul>
        <a class="more">more...</a>
      </div>
    </section>

    <section class="carousel">
      <svg class="carousel-arrow" style="left:43px" width="16" height="34" viewBox="0 0 16 34"><polyline points="14,2 2,17 14,32" fill="none" stroke="#fff" stroke-width="2"/></svg>
      <div class="slide" style="left:127px"><div class="slide-image" role="img" aria-label="Example photo"></div><p class="slide-title">Lorem ipsum</p></div>
      <div class="slide" style="left:305px"><div class="slide-image" role="img" aria-label="Example photo"></div><p class="slide-title">Lorem ipsum</p></div>
      <div class="slide" style="left:482px"><div class="slide-image" role="img" aria-label="Example photo"></div><p class="slide-title">Lorem ipsum</p></div>
      <svg class="carousel-arrow" style="left:633px" width="16" height="34" viewBox="0 0 16 34"><polyline points="2,2 14,17 2,32" fill="none" stroke="#fff" stroke-width="2"/></svg>
    </section>
  </main>

  <footer class="site-footer">
    <div class="footer-mark"></div>
    <div class="footer-group" style="left:211px; top:28px">
      <h3>Pedagogical entrepreneurship</h3>
      <p>What is pedagogical entrepreneurship? &nbsp;| &nbsp;Science &nbsp;| &nbsp;Best pratice schools &nbsp;| &nbsp;Lurvikmeteret &nbsp;| &nbsp;About lurvik.no</p>
      <h3>Gode eksempler</h3>
      <p>Små-TOPP at Vassbygd school &nbsp;| &nbsp;Små-TOPP at Vassbygd school &nbsp;| &nbsp;Små-TOPP at Vassbygd school &nbsp;| &nbsp;more...</p>
    </div>
    <div class="footer-group" style="left:714px; top:28px">
      <h3>Teaching Plans</h3>
      <p>Lorem Ipsum &nbsp;| &nbsp;Lorem Ipsum &nbsp;| &nbsp;Lorem Ipsum &nbsp;| &nbsp;Lorem Ipsum &nbsp;| &nbsp;more...</p>
      <h3>Methods</h3>
      <p>Story line &nbsp;| &nbsp;<b>TOPP</b> &nbsp;| &nbsp;Café-pedagogikk &nbsp;| &nbsp;more...</p>
    </div>
  </footer>

</div>
</body>
</html>
```